Business Card Design Project

Business card based on attached logo

Todd Merrick
Todd@lorvantest.com
877-514-9073 ext. 318
Www.LorvanTest.com

Industry/Entity Type

Business

```html
<!DOCTYPE html>
<html lang="en">
<head>
<meta charset="utf-8">
<title>LorvanTest Business Cards</title>
<link href="https://fonts.googleapis.com/css2?family=Jost:wght@400;500;600;700&display=swap" rel="stylesheet">
<style>
  :root {
    --red: #ed1c24;
    --ink: #231f20;
    --paper: #ffffff;
    --table: #e9e6e1;
    --rule: #bdbdbd;
  }
  * { margin: 0; padding: 0; box-sizing: border-box; }
  html, body { width: 1200px; height: 715px; overflow: hidden; }
  body {
    position: relative;
    background: var(--table);
    font-family: "Jost", sans-serif;
    color: var(--ink);
  }
  .card {
    position: absolute;
    width: 508px;
    height: 290px;
    overflow: hidden;
    box-shadow: 0 2px 6px rgba(0,0,0,0.18);
  }
  .card--front { left: 51px; top: 36px; background: var(--paper); }
  .card--back-white { left: 623px; top: 36px; background: var(--paper); }
  .card--back-red { left: 47px; top: 378px; background: var(--red); }
  .card--back-black { left: 628px; top: 381px; background: var(--ink); }

  /* front */
  .brand {
    position: absolute;
    left: 40px;
    top: 100px;
    display: flex;
    align-items: center;
    gap: 8px;
  }
  .brand__name {
    font-size: 34px;
    font-weight: 700;
    color: var(--ink);
    letter-spacing: -0.5px;
  }
  .brand__mark {
    width: 16px;
    height: 16px;
    background: var(--red);
  }
  .divider {
    position: absolute;
    left: 255px;
    top: 66px;
    width: 1px;
    height: 126px;
    background: var(--rule);
  }
  .person {
    position: absolute;
    left: 276px;
    top: 72px;
  }
  .person__name {
    font-size: 20px;
    font-weight: 600;
    color: var(--red);
    letter-spacing: 0.6px;
    margin-bottom: 18px;
  }
  .contact {
    list-style: none;
  }
  .contact__item {
    display: flex;
    align-items: center;
    gap: 6px;
    font-size: 13.5px;
    line-height: 24.5px;
  }
  .contact__icon { width: 10px; height: 10px; flex: none; }
  .band {
    position: absolute;
    left: 0;
    bottom: 0;
    width: 100%;
    height: 36px;
    display: flex;
  }
  .band__dark { width: 233px; background: var(--ink); }
  .band__gap {
    width: 53px;
    display: flex;
    align-items: center;
    justify-content: center;
    background: var(--paper);
  }
  .band__square { width: 18px; height: 18px; background: var(--red); }
  .band__red { flex: 1; background: var(--red); }

  /* backs */
  .back-brand {
    position: absolute;
    left: 0;
    right: 0;
    top: 96px;
    display: flex;
    align-items: center;
    justify-content: center;
    gap: 12px;
  }
  .back-brand__name {
    font-size: 56px;
    font-weight: 700;
    letter-spacing: -1px;
  }
  .back-brand__mark { width: 26px; height: 26px; }
  .back-url {
    position: absolute;
    left: 0;
    right: 0;
    bottom: 18px;
    text-align: center;
    font-size: 15px;
    letter-spacing: 3px;
  }
  .card--back-white .back-brand__name { color: var(--red); }
  .card--back-white .back-brand__mark { background: var(--red); }
  .card--back-white .back-url { color: var(--ink); }
  .card--back-red .back-brand__name,
  .card--back-black .back-brand__name,
  .card--back-red .back-url,
  .card--back-black .back-url { color: var(--paper); }
  .card--back-red .back-brand__mark,
  .card--back-black .back-brand__mark { background: var(--paper); }
</style>
</head>
<body>

<section class="card card--front">
  <div class="brand">
    <span class="brand__name">LorvanTest</span>
    <span class="brand__mark"></span>
  </div>
  <div class="divider"></div>
  <div class="person">
    <p class="person__name">Todd Merrick</p>
    <ul class="contact">
      <li class="contact__item">
        <svg class="contact__icon" viewBox="0 0 10 10" aria-hidden="true"><path d="M2 0.5 L3.8 2.6 L2.8 3.8 Q4 6 6.2 7.2 L7.4 6.2 L9.5 8 L8.2 9.5 Q1 8 0.5 1.8 Z" fill="#ed1c24"/></svg>
        877-514-9073 ext. 318
      </li>
      <li class="contact__item">
        <svg class="contact__icon" viewBox="0 0 10 10" aria-hidden="true"><rect x="0.5" y="2" width="9" height="6.5" fill="#ed1c24"/><path d="M0.8 2.3 L5 5.6 L9.2 2.3" fill="none" stroke="#fff" stroke-width="0.9"/></svg>
        Todd@lorvantest.com
      </li>
      <li class="contact__item">
        <svg class="contact__icon" viewBox="0 0 10 10" aria-hidden="true"><circle cx="5" cy="5" r="4.3" fill="none" stroke="#ed1c24" stroke-width="1"/><ellipse cx="5" cy="5" rx="1.8" ry="4.3" fill="none" stroke="#ed1c24" stroke-width="0.8"/><path d="M0.7 5 H9.3" stroke="#ed1c24" stroke-width="0.8"/></svg>
        www.LorvanTest.com
      </li>
    </ul>
  </div>
  <div class="band">
    <div class="band__dark"></div>
    <div class="band__gap"><span class="band__square"></span></div>
    <div class="band__red"></div>
  </div>
</section>

<section class="card card--back-white">
  <div class="back-brand">
    <span class="back-brand__name">LorvanTest</span>
    <span class="back-brand__mark"></span>
  </div>
  <p class="back-url">www.LorvanTest.com</p>
</section>

<section class="card card--back-red">
  <div class="back-brand">
    <span class="back-brand__name">LorvanTest</span>
    <span class="back-brand__mark"></span>
  </div>
  <p class="back-url">www.LorvanTest.com</p>
</section>

<section class="card card--back-black">
  <div class="back-brand">
    <span class="back-brand__name">LorvanTest</span>
    <span class="back-brand__mark"></span>
  </div>
  <p class="back-url">www.LorvanTest.com</p>
</section>

</body>
</html>
```